Modern, clean and professional Wordpress design for a safety training company!

We are currently in the process of creating a new website for our business. We have hired a website developer and the main structure of our new Wordpress site is complete. We now need an overall design plan for the site. We need a very clean, professional and easy to follow website. Most of our website visitors only spend about 30-45 secs on our sites "shopping " so it is imperative that we have a strong Home Page.
Our company specializes in CPR and First Aid Certification Classes to businesses and individuals throughout Northern California. We provide these certifications two ways: ONSITE-We come to you, and HOSTED-we offer weekly classes at our 2 locations.
Our design needs to use the general green and blue colors of our logo. But we also like white.
The final design MUST communicate a legitimate, trustworthy and professional business. Our industry is VERY competitive and we need to STAND OUT.
Currently, the NEW website that we need a new design for is www.LifelineDrillWorks.com
Our old website is www.RescuePrepValleyHub.com and we really do like the design of this website, but we just needed a Wordpress site for SEO purposes.
These are 3 websites that we really:
http://morvaliontech.com/
http://www.tralbex.com/
https://www.plivant.com/
I have attached our Logo and other images if you need to use them but looking at the current two sites will be you best help.
Target Market(s)
1) Large businesses and industries that are looking for a company to provide ONSITE safety training classes at their office or place of work.
2) Individuals that need certifications for their jobs and other needs. These individuals are looking for a legitimate, trustworthy and professional environment to complete their training class.

```html
<!DOCTYPE html>
<html lang="en">
<head>
<meta charset="utf-8">
<title>Lifeline Drill Works – CPR and First Aid</title>
<link rel="stylesheet" href="https://fonts.googleapis.com/css2?family=Raleway:wght@400;500;600&family=Open+Sans:wght@400;600&display=swap">
<style>
:root{
  --navy:#0e2a85;
  --navy-dark:#0a1f6b;
  --lime:#8cc21f;
  --lime-light:#a9d43a;
  --ink:#222;
  --body:#444;
  --muted:#8a8a8a;
  --link:#1d3c8f;
  --page:#f4f5f7;
  --panel:#e6e6e8;
  --white:#fff;
}
*{box-sizing:border-box;margin:0;padding:0}
html,body{width:786px;height:1200px;overflow:hidden}
body{position:relative;background:var(--page);font-family:"Open Sans",sans-serif;color:var(--body)}
.abs{position:absolute}
.topline{left:0;top:0;width:786px;height:2px;background:var(--navy-dark)}
.brand{left:40px;top:34px;font-family:"Raleway",sans-serif;font-weight:600;font-size:21px;color:var(--navy);display:flex;align-items:center;gap:9px}
.brand .dot{width:16px;height:16px;border-radius:50%;background:var(--lime)}
.contact{right:38px;top:28px;font-size:11.5px;color:#333;display:flex;align-items:center;gap:6px}
.contact svg{width:10px;height:10px}
.nav{left:223px;top:65px;display:flex;gap:24px;font-family:"Raleway",sans-serif;font-weight:500;font-size:11.6px;color:#222}
.nav .active{color:var(--navy);position:relative}
.nav .active::after{content:"";position:absolute;left:-4px;right:-4px;top:29px;height:5px;background:var(--navy)}

/* image areas: soft tonal fills */
.hero{left:0;top:101px;width:786px;height:333px;
  background:
    radial-gradient(ellipse 260px 120px at 170px 40px,rgba(235,240,246,.95),transparent 70%),
    radial-gradient(ellipse 200px 110px at 640px 70px,rgba(220,226,232,.8),transparent 70%),
    radial-gradient(ellipse 180px 90px at 470px 250px,rgba(150,95,70,.55),transparent 70%),
    radial-gradient(ellipse 220px 100px at 690px 280px,rgba(110,80,60,.6),transparent 70%),
    radial-gradient(ellipse 160px 80px at 270px 290px,rgba(120,85,60,.55),transparent 70%),
    linear-gradient(180deg,#cfd6df 0%,#b8bfc8 30%,#8c8682 60%,#5e5048 100%)}
.tagline{left:39px;top:154px;width:263px;height:100px;background:var(--navy);color:var(--white);padding:20px 16px}
.tagline small{display:block;font-family:"Raleway",sans-serif;font-size:14.5px;letter-spacing:.2px}
.tagline strong{display:block;font-family:"Raleway",sans-serif;font-weight:600;font-size:26px;margin-top:5px;letter-spacing:-.2px}
.learn{left:39px;top:254px;width:98px;height:38px;background:var(--lime);color:var(--white);font-family:"Raleway",sans-serif;font-weight:600;font-size:10.8px;display:flex;align-items:center;justify-content:center}
.dots{left:39px;top:311px;display:flex;gap:11px}
.dots i{width:7px;height:7px;border-radius:50%;background:rgba(255,255,255,.6)}
.dots i.on{background:var(--white)}

.sheet{left:39px;top:358px;width:708px;height:638px;background:var(--white);border-top:3px solid var(--navy);box-shadow:0 2px 6px rgba(0,0,0,.15)}
.card{top:375px;width:217px;height:171px;box-shadow:0 6px 6px -4px rgba(0,0,0,.25)}
.card .photo{height:131px}
.card .label{height:40px;background:var(--navy);color:var(--white);font-family:"Raleway",sans-serif;font-weight:500;font-size:19px;padding:8px 13px}
.card.green .label{background:linear-gradient(var(--lime-light),var(--lime))}
.photo.scrubs{background:
  radial-gradient(ellipse 60px 50px at 40px 40px,rgba(225,190,160,.8),transparent 70%),
  radial-gradient(ellipse 70px 60px at 180px 45px,rgba(230,200,175,.7),transparent 70%),
  radial-gradient(ellipse 110px 60px at 150px 110px,#7a86cf,transparent 75%),
  linear-gradient(160deg,#d7dce6,#a3abd2 50%,#6f7cc0)}
.photo.aid{background:
  radial-gradient(ellipse 70px 45px at 170px 40px,rgba(220,185,130,.8),transparent 70%),
  radial-gradient(ellipse 90px 70px at 120px 90px,#3a3a3e,transparent 75%),
  linear-gradient(135deg,#8a8a8c,#4a4a4e 45%,#1f1f23)}
.photo.outdoor{background:
  radial-gradient(ellipse 70px 60px at 200px 50px,#4f7a2c,transparent 75%),
  radial-gradient(ellipse 60px 40px at 130px 50px,rgba(200,200,200,.9),transparent 70%),
  radial-gradient(ellipse 45px 55px at 50px 70px,rgba(240,210,215,.9),transparent 70%),
  linear-gradient(180deg,#c8c8c2 0%,#9aa08c 55%,#5d7a38 100%)}

h2{font-family:"Raleway",sans-serif;font-weight:500;font-size:22.5px;color:var(--ink);letter-spacing:-.2px}
.intro{left:54px;top:636px;width:306px;font-size:8.8px;line-height:14.5px;color:#333}
.intro p+p{margin-top:14.5px}
.video{left:391px;top:587px;width:339px;height:189px;background:
  radial-gradient(ellipse 90px 80px at 90px 40px,rgba(245,245,242,.95),transparent 70%),
  radial-gradient(ellipse 120px 50px at 100px 150px,rgba(90,90,120,.6),transparent 70%),
  radial-gradient(ellipse 130px 55px at 250px 145px,rgba(70,90,60,.55),transparent 70%),
  linear-gradient(180deg,#e2e2df 0%,#c9c7c2 40%,#7a746e 70%,#3d3a36 100%)}
.video .bar{position:absolute;left:0;bottom:0;width:100%;height:28px;background:rgba(10,10,10,.85)}
.video .track{position:absolute;left:56px;top:11px;width:208px;height:6px;background:#555}
.video .track b{display:block;width:58px;height:100%;background:var(--lime)}
.video .hd{position:absolute;right:22px;top:7px;font-size:9px;font-weight:600;font-style:italic;color:var(--lime)}
.video .tools{position:absolute;right:6px;top:7px;display:flex;flex-direction:column;gap:4px}
.video .tools i{width:28px;height:20px;background:rgba(20,20,20,.85);border-radius:2px;color:#fff;font-style:normal;font-size:4.5px;text-align:center;padding-top:12px;line-height:6px}

.cert{top:848px;width:329px;height:124px;background:var(--panel)}
.cert .thumb{position:absolute;left:10px;top:14px;width:86px;height:68px;border:3px solid var(--white)}
.thumb.unit{background:
  radial-gradient(ellipse 22px 30px at 45px 40px,#5a74a8,transparent 75%),
  linear-gradient(90deg,#6a6a6a,#cfcfcf 35%,#e4e4e4 70%,#9a9a9a)}
.thumb.room{background:
  radial-gradient(ellipse 50px 18px at 40px 50px,#2a2a2a,transparent 80%),
  linear-gradient(180deg,#f0f0f0 0%,#e2e2e2 45%,#6a6a6a 80%,#3a3a3a)}
.cert h3{position:absolute;left:110px;top:12px;font-family:"Raleway",sans-serif;font-weight:500;font-size:20px;color:var(--navy)}
.cert p{position:absolute;left:110px;top:44px;width:198px;font-size:8.2px;line-height:12px;color:var(--muted)}
.cert .btn{position:absolute;left:110px;top:85px;padding:0 6px;height:25px;line-height:25px;background:var(--navy);color:var(--white);font-size:10px;border-radius:2px}

.fcol{top:1022px}
.fcol h4{font-family:"Raleway",sans-serif;font-weight:400;font-size:15px;color:#333;margin-bottom:10px}
.fcol a{display:block;font-size:8.8px;line-height:14.5px;color:var(--link);text-decoration:none}
.rule{left:39px;top:1150px;width:708px;height:1px;background:#ddd}
.copy{left:39px;top:1167px;font-size:8.8px;color:#333}
.social{right:40px;top:1161px;display:flex;gap:3px}
.social i{width:20px;height:20px;border-radius:4px;background:var(--navy)}
</style>
</head>
<body>
<div class="abs topline"></div>
<header>
  <div class="abs brand"><span class="dot"></span>Lifeline Drill Works</div>
  <div class="abs contact">
    <svg viewBox="0 0 10 10"><rect width="10" height="10" rx="1.5" fill="#222"/><path d="M3 2.5l1 1.5-.6.6a4 4 0 0 0 2 2l.6-.6 1.5 1-.6 1A5 5 0 0 1 2 3.1z" fill="#fff"/></svg>
    Call us: 916-555-0187 &nbsp;|&nbsp;
    <svg viewBox="0 0 10 10"><rect width="10" height="10" rx="1.5" fill="#222"/><rect x="2" y="3" width="6" height="4" fill="#fff"/><path d="M2 3l3 2.2L8 3" stroke="#222" stroke-width=".7" fill="none"/></svg>
    info@lifelinedrill.com
  </div>
  <nav class="abs nav">
    <span class="active">HOME</span><span>CLASS CALENDER</span><span>CLASSES FOR GROUPS</span><span>CERTIFICATION CLASSES</span><span>ABOUT US</span>
  </nav>
</header>

<section>
  <div class="abs hero" role="img" aria-label="Photo of a classroom full of students attending a training session"></div>
  <div class="abs tagline"><small>SPECIALIZES IN</small><strong>CPR AND FIRST AID</strong></div>
  <div class="abs learn">LEARN MORE</div>
  <div class="abs dots"><i></i><i class="on"></i><i></i></div>
</section>

<div class="abs sheet"></div>

<div class="abs card green" style="left:52px"><div class="photo scrubs" role="img" aria-label="Photo of medical staff practising on a patient"></div><div class="label">CPR</div></div>
<div class="abs card" style="left:284px"><div class="photo aid" role="img" aria-label="Photo of a responder kneeling to give first aid"></div><div class="label">FIRST AID</div></div>
<div class="abs card" style="left:514px"><div class="photo outdoor" role="img" aria-label="Photo of a student practising chest compressions outdoors"></div><div class="label">CLASSES</div></div>

<h2 class="abs" style="left:52px;top:591px">WELCOME TO CPR</h2>
<div class="abs intro">
  <p>Lifeline Drill Works is Northern California’s leader in CPR, BLS, and Basic First Aid Certifications! Taught by experienced Firefighters, our classes are much shorter and provide common sense knowledge and skills to each student to help prepare them for actual emergencies.</p>
  <p>By using real life emergency responders, we have revolutionized the standard, boring CPR class by teaching students the need-to-know information and preparing them with facts and tips to help them in true life and death situations!</p>
</div>
<div class="abs video" role="img" aria-label="Video of an instructor teaching a class of students">
  <div class="tools"><i>LIKE</i><i>LATER</i><i>SHARE</i><i>EMBED</i></div>
  <div class="bar">
    <svg style="position:absolute;left:22px;top:8px" width="10" height="12" viewBox="0 0 10 12"><path d="M0 0l10 6-10 6z" fill="#fff"/></svg>
    <div class="track"><b></b></div>
    <span class="hd">HD</span>
  </div>
</div>

<h2 class="abs" style="left:54px;top:803px">OUR CERTIFICATIONS</h2>
<div class="abs cert" style="left:55px">
  <div class="thumb unit" role="img" aria-label="Photo of a defibrillator unit in an office"></div>
  <h3>ONSITE</h3>
  <p>Lifeline Drill Works has provided CPR, BLS and First Aid classes to thousands of individuals and businesses ...</p>
  <span class="btn">Read More</span>
</div>
<div class="abs cert" style="left:401px">
  <div class="thumb room" role="img" aria-label="Photo of a training room with rows of chairs"></div>
  <h3>HOSTED</h3>
  <p>Lifeline Drill Works has provided CPR, BLS and First Aid classes to thousands of individuals and businesses ...</p>
  <span class="btn">Read More</span>
</div>

<footer>
  <div class="abs fcol" style="left:40px"><h4>ABOUT US</h4><a>Mission &amp; Values</a><a>Leadership</a><a>Careers</a><a>Accreditations</a></div>
  <div class="abs fcol" style="left:173px"><h4>INVESTORS</h4><a>Business Overview</a><a>Therapeutic Pipeline</a><a>Video Library</a><a>Corporate Presentations</a><a>Webcasts</a></div>
  <div class="abs fcol" style="left:336px"><h4>THERAPEUTIC</h4><a>Clinical Pipeline</a><a>OpFlowKit®</a><a>CellBase™</a><a>OpFlowKit</a><a>Our Laboratories</a></div>
  <div class="abs fcol" style="left:493px"><h4>THERAPEUTIC</h4><a>ThermaFlow® (TFX)</a><a>ThermaFlow® (CoreFlow)</a><a>Vanta BMC</a><a>Sterile, Manual Systems</a><a>ColdVault Storage</a></div>
  <div class="abs fcol" style="left:651px"><h4>CONTACT US</h4><a>Contact Details</a><a>Support</a><a>How To Order</a></div>
  <div class="abs rule"></div>
  <div class="abs copy">© 2015 lifelinedrillworks.com. All Right Reserved.</div>
  <div class="abs social"><i></i><i></i><i></i><i></i><i></i></div>
</footer>
</body>
</html>
```